Roofing Contractor business card redesign

I want to redesign my business card with a fresh, eye catching concept

Target Market(s)

Residential Roofing Clients, potential employees, and subcontractors.

Industry/Entity Type

Business

Colors

Designer to choose colors to be used in the design.

Requirements
Nice to have
• I just want something that's more pleasing to the eye. You can use a combination of either / or of my logos.

```html
<!DOCTYPE html>
<html lang="en">
<head>
<meta charset="utf-8">
<title>Fair Hands Contractors – Business Card</title>
<link rel="stylesheet" href="https://fonts.googleapis.com/css2?family=Roboto:wght@400;700;900&display=swap">
<style>
  :root {
    --backdrop: #e9e4de;
    --card-white: #fbfbfa;
    --maroon: #4a2327;
    --maroon-text: #5a1f24;
    --ink-light: #f4efec;
    --grey-text: #6f6a67;
    --art-orange: #e8852f;
    --art-yellow: #f2b531;
  }
  * { box-sizing: border-box; margin: 0; padding: 0; }
  html, body {
    width: 1200px; height: 911px; overflow: hidden;
    background: var(--backdrop);
    font-family: "Roboto", Arial, sans-serif;
  }
  .stage { position: relative; width: 1200px; height: 911px; }
  .card {
    position: absolute;
    border-radius: 22px;
    overflow: hidden;
    background: var(--card-white);
    box-shadow: 0 14px 30px rgba(60, 40, 30, 0.25);
  }

  /* Front (portrait) */
  .card-front { left: 120px; top: 165px; width: 340px; height: 580px; }
  .front-art {
    position: absolute; left: 0; top: 0; width: 100%; height: 232px;
    display: flex; align-items: flex-end; justify-content: center;
  }
  .front-art .art-block {
    width: 250px; height: 196px;
    border-radius: 90px 90px 0 0;
    background: linear-gradient(160deg, var(--art-yellow) 0%, var(--art-orange) 55%, #b45a22 100%);
  }
  .front-info {
    position: absolute; left: 0; top: 232px; width: 100%; bottom: 0;
    background: var(--maroon);
    color: var(--ink-light);
    text-align: center;
    padding-top: 38px;
  }
  .person-name { font-weight: 700; font-size: 21px; letter-spacing: 0.5px; }
  .person-role { font-size: 15px; line-height: 1.3; margin-top: 4px; }
  .address { font-size: 14px; line-height: 1.35; margin-top: 20px; }
  .contact { font-size: 14px; line-height: 1.45; margin-top: 20px; }
  .contact b { font-weight: 700; }

  /* Back (landscape) */
  .card-back { left: 520px; top: 285px; width: 560px; height: 340px; }
  .web-vertical {
    position: absolute; left: 42px; top: 50%;
    transform: translate(-50%, -50%) rotate(90deg);
    font-size: 13px; letter-spacing: 6px; color: var(--grey-text);
    white-space: nowrap;
  }
  .brand {
    position: absolute; left: 70px; right: 0; top: 0; bottom: 0;
    display: flex; align-items: center; justify-content: center; gap: 14px;
  }
  .brand-dot {
    width: 30px; height: 30px; border-radius: 50%;
    background: var(--art-orange);
    flex: none;
  }
  .brand-name {
    font-weight: 900; font-size: 38px; line-height: 1;
    color: var(--maroon-text);
    white-space: nowrap;
  }
</style>
</head>
<body>
<main class="stage">
  <section class="card card-front">
    <div class="front-art">
      <div class="art-block" role="img" aria-label="Illustration of three friendly tradesmen holding a hammer, a clipboard and tools"></div>
    </div>
    <div class="front-info">
      <p class="person-name">SAM ROWLEY</p>
      <p class="person-role">Keller Certified Roof Inspector<br>Licensed Property Adjuster</p>
      <p class="address">4210 Cedar Lane Suite 118<br>Plano, TX 75024</p>
      <p class="contact">
        <b>P:</b> (555) 014-2290<br>
        <b>C:</b> (555) 017-6631 <b>E:</b> sam@fairhandstx.com<br>
        <b>W:</b> www.fairhandstx.com
      </p>
    </div>
  </section>

  <section class="card card-back">
    <p class="web-vertical">www.fairhandstx.com</p>
    <div class="brand">
      <span class="brand-dot"></span>
      <p class="brand-name">Fair Hands Contractors</p>
    </div>
  </section>
</main>
</body>
</html>
```